Website for enterprise software start-up

We need a new Wordpress website. We are an early stage start-up focused on mobile video technology for cellular operators. The audience is strategy, marketing and customer acquisition execs from the operators.

The purpose of the site is to act as a sales brochure and capture leads. A demo app can be downloaded from the current site, want to put that behind a contact form.

Current website is at www.velmora.tv. Similar number of pages. Looking for a clean design template, with minimal customization. Blog will remain as is.

Want to be able to modify the copy via Wordpress. Reference designs I like: quandrix.com, briskfold7metrics.com

Target Market(s)

Mobile operators and MVNOs in the US and Asia Pacific regions

Industry/Entity Type

Business Software

Coding

Coded - Design and coding required

Number of Pages Required

4 page

Font styles to use
Sans Serif

Colors
f78f20

Requirements
Must have
• Form for downloading sample apps.
• Landing page with image, Product, Blog, About, Contact
• Team page

```html
<!DOCTYPE html>
<html lang="en">
<head>
<meta charset="utf-8">
<title>Velmora Media</title>
<link rel="stylesheet" href="https://fonts.googleapis.com/css2?family=Raleway:wght@500;600;700;800&family=Open+Sans:wght@400;600;700&display=swap">
<style>
:root{
  --orange:#e3701a;
  --ink:#1d1d1d;
  --text:#4a4a4a;
  --line:#cfcfcf;
  --grey-bg:#f1f1f1;
  --dark:#2b2b2b;
  --white:#fff;
  --field:#f4f4f4;
}
*{box-sizing:border-box;margin:0;padding:0}
html,body{width:1200px;height:2922px;overflow:hidden}
body{position:relative;font-family:"Open Sans",Arial,sans-serif;color:var(--text);background:var(--white)}

/* header */
.site-header{position:absolute;top:0;left:0;width:1200px;height:85px;background:var(--white);box-shadow:0 2px 6px rgba(0,0,0,.12);z-index:3}
.brand{position:absolute;left:163px;top:0;height:85px;display:flex;align-items:center;gap:10px}
.brand-dot{width:14px;height:14px;background:var(--ink)}
.brand-name{font-family:"Raleway",Arial,sans-serif;font-weight:800;font-size:34px;color:var(--ink);line-height:1}
.main-nav{position:absolute;right:160px;top:0;height:85px;display:flex;gap:32px;align-items:center}
.main-nav a{font-family:"Raleway",Arial,sans-serif;font-weight:700;font-size:14px;color:var(--ink);text-decoration:none;position:relative}
.main-nav a.active{color:var(--orange)}
.main-nav a.active::before{content:"";position:absolute;left:0;right:0;top:-14px;height:3px;background:var(--orange)}

/* hero */
.hero{position:absolute;top:85px;left:0;width:1200px;height:443px;background:linear-gradient(100deg,#6b5a4d 0%,#b79479 35%,#d8b596 55%,#c89373 75%,#b27a58 100%)}
.hero-title{position:absolute;top:140px;width:100%;text-align:center;font-family:"Raleway",Arial,sans-serif;font-weight:700;font-size:34px;color:var(--white);text-shadow:0 2px 4px rgba(0,0,0,.35)}
.hero-sub{position:absolute;top:195px;width:100%;text-align:center;font-family:"Raleway",Arial,sans-serif;font-weight:700;font-size:19px;line-height:24px;color:var(--white);text-shadow:0 1px 3px rgba(0,0,0,.4)}
.btn-start{position:absolute;left:510px;top:270px;width:180px;height:46px;background:var(--orange);color:var(--white);font-family:"Raleway",Arial,sans-serif;font-weight:700;font-size:22px;display:flex;align-items:center;justify-content:center}
.slider-dots{position:absolute;top:412px;left:0;width:100%;display:flex;justify-content:center;gap:6px}
.slider-dots span{width:11px;height:11px;border-radius:50%;background:var(--white)}
.slider-dots span.on{background:transparent;border:2px solid var(--white)}

/* section headings */
.section-title{position:absolute;width:100%;text-align:center;font-family:"Raleway",Arial,sans-serif;font-weight:800;font-size:26px;color:var(--ink)}
.section-title em,.feature-title em{font-style:normal;color:var(--orange)}
.title-rule{position:absolute;left:0;width:1200px;height:20px}

.welcome-text{position:absolute;left:170px;top:634px;width:860px;text-align:center;font-size:11.5px;line-height:22px;color:var(--text)}

/* feature blocks */
.photo{position:absolute}
.feature-panel{position:absolute;background:var(--grey-bg);overflow:hidden}
.feature-title{font-family:"Raleway",Arial,sans-serif;font-weight:800;font-size:27px;color:var(--ink)}
.feature-rule{height:2px;background:#ccc;margin-top:10px;position:relative;width:375px}
.feature-rule::before{content:"";position:absolute;left:0;top:0;width:70px;height:2px;background:var(--orange)}
.feature-lead{margin-top:20px;font-size:14.5px;line-height:24px;font-weight:700;color:var(--ink)}
.feature-list{list-style:none;margin-top:14px}
.feature-list li{display:flex;gap:16px;font-size:12.5px;line-height:21px;color:var(--text);margin-bottom:22px}
.feature-list svg{flex:none;margin-top:3px}

/* clients */
.clients-row{position:absolute;top:1945px;left:110px;width:980px;display:flex;align-items:center;justify-content:space-between}
.arrow-btn{width:28px;height:30px;background:#8a8a8a;display:flex;align-items:center;justify-content:center}
.client-box{width:140px;height:68px;border:1px solid #bdbdbd;display:flex;align-items:center;justify-content:center;font-weight:700;font-size:14px;color:#9a9a9a}

/* partner */
.partner{position:absolute;top:2060px;left:0;width:1200px;height:208px;background:var(--grey-bg)}
.partner-badge{position:absolute;left:487px;top:44px;width:226px;height:78px;border-radius:6px;background:#dcdcdc}
.partner-text{position:absolute;top:143px;width:100%;text-align:center;font-size:18px;font-weight:600;color:var(--ink)}
.partner-text a{color:var(--orange);text-decoration:none}

/* downloads */
.downloads{position:absolute;top:2268px;left:0;width:1200px;height:208px;background:linear-gradient(90deg,#3a312c,#5a4c44 40%,#6b5c53 60%,#3e3430)}
.downloads-title{position:absolute;top:44px;width:100%;text-align:center;font-family:"Raleway",Arial,sans-serif;font-weight:700;font-size:24px;color:var(--white)}
.store-btn{position:absolute;top:102px;width:134px;height:44px;background:#111;border:1px solid #777;border-radius:4px;color:var(--white);display:flex;align-items:center;gap:8px;padding-left:12px}
.store-btn i{width:14px;height:14px;background:#ddd;flex:none}
.store-btn small{display:block;font-size:8px;line-height:10px}
.store-btn b{display:block;font-size:13px;line-height:16px;font-weight:600}

/* contact form */
.contact{position:absolute;top:2476px;left:0;width:1200px;height:396px;background:var(--orange)}
.mail-badge{position:absolute;left:557px;top:-40px;width:86px;height:86px;border-radius:50%;background:var(--dark);border:4px solid var(--white);display:flex;align-items:center;justify-content:center}
.field{position:absolute;background:var(--field);font-size:14px;font-weight:600;color:#555;padding:18px 16px}
.btn-submit{position:absolute;left:549px;top:335px;width:104px;height:40px;background:var(--dark);color:var(--white);font-size:16px;font-weight:700;display:flex;align-items:center;justify-content:center}

/* footer */
.site-footer{position:absolute;top:2872px;left:0;width:1200px;height:50px;background:var(--dark)}
.copyright{position:absolute;left:165px;top:17px;font-size:10.5px;color:#ddd}
.social{position:absolute;right:160px;top:16px;display:flex;gap:14px}
.social span{display:flex;align-items:center;gap:5px;font-size:10.5px;color:#ddd}
.social i{width:12px;height:12px;border-radius:50%;background:#888}
</style>
</head>
<body>

<header class="site-header">
  <div class="brand">
    <div class="brand-dot"></div>
    <div class="brand-name">Velmora Media</div>
  </div>
  <nav class="main-nav">
    <a class="active">HOME</a><a>ABOUT US</a><a>PRODUCT</a><a>OUR TEAM</a><a>BLOG</a><a>CONTACT US</a>
  </nav>
</header>

<section class="hero" role="img" aria-label="Photo of a hand holding a smartphone, soft warm tones">
  <h1 class="hero-title">High Quality Mobile Engagement</h1>
  <p class="hero-sub">We Engage Mobile Audiences With The Right Video Content<br>At The Perfect Moment</p>
  <div class="btn-start">Get Started</div>
  <div class="slider-dots"><span class="on"></span><span></span><span></span><span></span></div>
</section>

<h2 class="section-title" style="top:557px">WELCOME TO <em>VELMORA MEDIA</em></h2>
<svg class="title-rule" style="top:595px" viewBox="0 0 1200 20" width="1200" height="20">
  <line x1="390" y1="10" x2="810" y2="10" stroke="#cfcfcf" stroke-width="1"/>
  <circle cx="600" cy="10" r="5" fill="#e3701a"/>
</svg>
<p class="welcome-text">Lorem ipsum dolor sit amet, consectetuer adipiscing elit, sed diam nonummy nibh euismod tincidunt ut laoreet dolore magna aliquam erat volutpat. Ut wisi enim ad minim veniam, quis nostrud exerci tation ullamcorper suscipit lobortis nisl ut aliquip ex ea commodo consequat. Duis autem vel eum iriure dolor in hendrerit in vulputate velit esse molestie consequat, vel illum dolore eu feugiat nulla facilisis at vero eros et accumsan et iusto odio dignissim qui blandit praesent luptatum zzril delenit augue duis dolore tefeugait nulla facilisi.</p>

<!-- push video notifications -->
<div class="photo" style="top:752px;left:0;width:600px;height:544px;background:linear-gradient(135deg,#d97a2e,#c9692a 45%,#b85a22)" role="img" aria-label="Photo of a white smartphone showing a lock screen with a video push notification, orange tint"></div>
<div class="feature-panel" style="top:752px;left:600px;width:600px;height:544px">
  <div style="position:absolute;left:36px;top:34px;width:440px">
    <h3 class="feature-title">PUSH VIDEO <em>NOTIFICATIONS</em></h3>
    <div class="feature-rule"></div>
    <p class="feature-lead">Personalised flawless HD videos, revealed at the perfect moment, as rich media notifications.</p>
    <ul class="feature-list">
      <li><svg width="14" height="14" viewBox="0 0 14 14"><rect x="1" y="1" width="12" height="12" fill="none" stroke="#e3701a" stroke-width="1.5"/><path d="M3.5 7l2.5 2.5 5-5.5" fill="none" stroke="#e3701a" stroke-width="1.8"/></svg><span>Reach your mobile audience with beautiful HD thumbnails and in-notification videos.</span></li>
      <li><svg width="14" height="14" viewBox="0 0 14 14"><rect x="1" y="1" width="12" height="12" fill="none" stroke="#e3701a" stroke-width="1.5"/><path d="M3.5 7l2.5 2.5 5-5.5" fill="none" stroke="#e3701a" stroke-width="1.8"/></svg><span>Instant video playback, zero buffering, guaranteed flawless playback - even when offline.</span></li>
      <li><svg width="14" height="14" viewBox="0 0 14 14"><rect x="1" y="1" width="12" height="12" fill="none" stroke="#e3701a" stroke-width="1.5"/><path d="M3.5 7l2.5 2.5 5-5.5" fill="none" stroke="#e3701a" stroke-width="1.8"/></svg><span>Content is personalised based on viewer interests and mobile viewing habits.</span></li>
      <li><svg width="14" height="14" viewBox="0 0 14 14"><rect x="1" y="1" width="12" height="12" fill="none" stroke="#e3701a" stroke-width="1.5"/><path d="M3.5 7l2.5 2.5 5-5.5" fill="none" stroke="#e3701a" stroke-width="1.8"/></svg><span>Monetize with beautiful HD preroll or interstitial ads.</span></li>
      <li><svg width="14" height="14" viewBox="0 0 14 14"><rect x="1" y="1" width="12" height="12" fill="none" stroke="#e3701a" stroke-width="1.5"/><path d="M3.5 7l2.5 2.5 5-5.5" fill="none" stroke="#e3701a" stroke-width="1.8"/></svg><span>Easily added to your existing apps within one hour.</span></li>
    </ul>
  </div>
</div>

<!-- native push video -->
<div class="feature-panel" style="top:1296px;left:0;width:600px;height:522px">
  <div style="position:absolute;left:163px;top:52px;width:400px">
    <h3 class="feature-title">NATIVE <em>PUSH VIDEO</em></h3>
    <div class="feature-rule"></div>
    <p class="feature-lead">Personalised flawless HD videos, discoverable in-app, and playable even when offline.</p>
    <ul class="feature-list">
      <li><svg width="14" height="14" viewBox="0 0 14 14"><rect x="1" y="1" width="12" height="12" fill="none" stroke="#e3701a" stroke-width="1.5"/><path d="M3.5 7l2.5 2.5 5-5.5" fill="none" stroke="#e3701a" stroke-width="1.8"/></svg><span>Guarantee your audience never gets frustrated with a poor quality mobile videostreaming experience.</span></li>
      <li><svg width="14" height="14" viewBox="0 0 14 14"><rect x="1" y="1" width="12" height="12" fill="none" stroke="#e3701a" stroke-width="1.5"/><path d="M3.5 7l2.5 2.5 5-5.5" fill="none" stroke="#e3701a" stroke-width="1.8"/></svg><span>Instant video playback, zero buffering, HD quality guaranteed - even when offline.</span></li>
      <li><svg width="14" height="14" viewBox="0 0 14 14"><rect x="1" y="1" width="12" height="12" fill="none" stroke="#e3701a" stroke-width="1.5"/><path d="M3.5 7l2.5 2.5 5-5.5" fill="none" stroke="#e3701a" stroke-width="1.8"/></svg><span>Content is personalised based on viewer interests and mobile viewing habits.</span></li>
      <li><svg width="14" height="14" viewBox="0 0 14 14"><rect x="1" y="1" width="12" height="12" fill="none" stroke="#e3701a" stroke-width="1.5"/><path d="M3.5 7l2.5 2.5 5-5.5" fill="none" stroke="#e3701a" stroke-width="1.8"/></svg><span>Monetize with beautiful HD preroll or interstitial ads.</span></li>
      <li><svg width="14" height="14" viewBox="0 0 14 14"><rect x="1" y="1" width="12" height="12" fill="none" stroke="#e3701a" stroke-width="1.5"/><path d="M3.5 7l2.5 2.5 5-5.5" fill="none" stroke="#e3701a" stroke-width="1.8"/></svg><span>Use your existing content management and hosting systems.</span></li>
    </ul>
  </div>
</div>
<div class="photo" style="top:1296px;left:600px;width:600px;height:522px;background:linear-gradient(135deg,#5a5a5a,#444 50%,#383838)" role="img" aria-label="Photo of two smartphones showing a list of movie trailer videos, dark grey tones"></div>

<!-- clients -->
<h2 class="section-title" style="top:1860px">OUR <em>CLIENTS</em></h2>
<svg class="title-rule" style="top:1897px" viewBox="0 0 1200 20" width="1200" height="20">
  <line x1="475" y1="10" x2="725" y2="10" stroke="#cfcfcf" stroke-width="1"/>
  <circle cx="600" cy="10" r="5" fill="#e3701a"/>
</svg>
<div class="clients-row">
  <div class="arrow-btn"><svg width="10" height="12" viewBox="0 0 10 12"><path d="M7 1L2 6l5 5" fill="none" stroke="#fff" stroke-width="2"/></svg></div>
  <div class="client-box">Tavrent TV</div>
  <div class="client-box">Brevant</div>
  <div class="client-box">Orvaline</div>
  <div class="client-box">Tavrent TV</div>
  <div class="client-box">Castelline Music</div>
  <div class="arrow-btn"><svg width="10" height="12" viewBox="0 0 10 12"><path d="M3 1l5 5-5 5" fill="none" stroke="#fff" stroke-width="2"/></svg></div>
</div>

<!-- partner -->
<section class="partner">
  <div class="partner-badge" role="img" aria-label="Certified developer partner badge"></div>
  <p class="partner-text"><a>Contact Us</a> For Details Of How To Become A Certified Developer Partner.</p>
</section>

<!-- downloads -->
<section class="downloads" role="img" aria-label="Dimmed photo of hands holding a phone">
  <h2 class="downloads-title">Fill Up The Form To Get Link For Downloading Sample Apps</h2>
  <div class="store-btn" style="left:450px"><i></i><div><small>Download on the</small><b>Appline Store</b></div></div>
  <div class="store-btn" style="left:616px"><i></i><div><small>GET IT ON</small><b>Playgrid</b></div></div>
</section>

<!-- contact form -->
<section class="contact">
  <div class="mail-badge">
    <svg width="40" height="28" viewBox="0 0 40 28"><rect x="1" y="1" width="38" height="26" rx="2" fill="#fff"/><path d="M2 2l18 14L38 2" fill="none" stroke="#2b2b2b" stroke-width="2"/></svg>
  </div>
  <div class="field" style="left:180px;top:66px;width:410px;height:58px">Your Name</div>
  <div class="field" style="left:610px;top:66px;width:410px;height:58px">Your Email</div>
  <div class="field" style="left:180px;top:136px;width:840px;height:58px">Subject</div>
  <div class="field" style="left:180px;top:204px;width:840px;height:120px">Message</div>
  <div class="btn-submit">Submit</div>
</section>

<footer class="site-footer">
  <p class="copyright">Copyright © 2016 Velmora Media. All Rights Reserved.</p>
  <div class="social">
    <span><i></i>Postwave</span><span><i></i>Chirply</span><span><i></i>Circlet</span><span><i></i>Netvine</span>
  </div>
</footer>

</body>
</html>
```